Marwick Law Letterhead

We need a new letterhead design for a Law Firm. The address for the law firm is 1475 Calloway Street, Suite 210, Houston, Texas 77041. Phone Number: 832-361-9027; Fax Number: 832-614-7359. The logo is uploaded to the project.

```html
<!DOCTYPE html>
<html lang="en">
<head>
<meta charset="utf-8">
<title>Marwick Law Letterhead</title>
<link rel="stylesheet" href="https://fonts.googleapis.com/css2?family=Open+Sans:wght@400;600&family=Arimo:wght@400&family=Pinyon+Script&display=swap">
<style>
  :root {
    --backdrop: #ececec;
    --paper: #e9e8ea;
    --navy: #0f1a4a;
    --red: #b0121b;
    --ink: #2a2a2e;
    --muted: #6d6d73;
    --rule: #9a9aa0;
  }
  * { box-sizing: border-box; margin: 0; padding: 0; }
  html, body {
    width: 1200px; height: 1012px; overflow: hidden;
    background: var(--backdrop);
  }
  .letterhead {
    position: absolute; left: 245px; top: 0;
    width: 710px; height: 1012px;
    background: var(--paper);
    overflow: hidden;
  }
  .brand {
    position: absolute; left: 53px; top: 62px;
    display: flex; align-items: center; gap: 12px;
  }
  .brand-square { width: 30px; height: 30px; background: var(--navy); }
  .brand-name {
    font-family: "Open Sans", sans-serif; font-weight: 600;
    font-size: 27px; color: var(--navy); letter-spacing: 0.3px;
  }
  .contact {
    position: absolute; top: 51px;
    font-family: "Open Sans", sans-serif; font-size: 12px;
    line-height: 14.6px; color: var(--muted); font-style: normal;
  }
  .contact-address { left: 321px; }
  .contact-divider {
    position: absolute; left: 466px; top: 46px;
    width: 1px; height: 62px; background: var(--rule);
  }
  .contact-lines { left: 485px; list-style: none; }
  .contact-lines li { display: flex; align-items: center; gap: 6px; }
  .contact-lines svg { width: 8px; height: 8px; fill: var(--navy); flex: none; }
  .letter {
    position: absolute; left: 76px; top: 238px; width: 558px;
    font-family: "Arimo", sans-serif; font-size: 11.6px;
    line-height: 16.9px; color: var(--ink); letter-spacing: -0.1px;
  }
  .letter p { margin-bottom: 16.9px; }
  .letter-body p { text-align: justify; }
  .letter-closing { margin-top: 45px; margin-bottom: 4px !important; }
  .letter-signature {
    font-family: "Pinyon Script", cursive; font-size: 23px;
    line-height: 28px; color: var(--ink);
  }
  .footer-rule {
    position: absolute; left: 0; bottom: 14px;
    width: 710px; height: 3px; background: var(--red);
  }
  .footer-band {
    position: absolute; left: 0; bottom: 0;
    width: 710px; height: 12px; background: var(--navy);
  }
</style>
</head>
<body>
<main class="letterhead">
  <header>
    <div class="brand">
      <span class="brand-square"></span>
      <span class="brand-name">Marwick Law</span>
    </div>
    <address class="contact contact-address">
      Marwick Law<br>
      1475 Calloway Street<br>
      Suite 210<br>
      Houston, Texas 77041
    </address>
    <span class="contact-divider"></span>
    <ul class="contact contact-lines">
      <li><svg viewBox="0 0 10 10" aria-hidden="true"><path d="M2 0.5 L4 2.8 L3 4 Q4.2 6 6 7 L7.2 6 L9.5 8 L8 9.6 Q3 9 0.4 2 Z"/></svg>832-361-9027</li>
      <li><svg viewBox="0 0 10 10" aria-hidden="true"><rect x="2.5" y="0.5" width="5" height="3"/><rect x="0.5" y="3.5" width="9" height="4"/><rect x="2.5" y="7" width="5" height="2.5"/></svg>832-614-7359</li>
      <li><svg viewBox="0 0 10 10" aria-hidden="true"><path d="M0.5 2 H9.5 V8 H0.5 Z M1 2.4 L5 5.6 L9 2.4" stroke="#e9e8ea" stroke-width="0.8"/></svg>contact@marwickinjury.com</li>
      <li><svg viewBox="0 0 10 10" aria-hidden="true"><circle cx="5" cy="5" r="4.5"/><path d="M0.5 5 H9.5 M5 0.5 Q2 5 5 9.5 Q8 5 5 0.5" stroke="#e9e8ea" stroke-width="0.7" fill="none"/></svg>www.marwickinjury.com</li>
    </ul>
  </header>

  <article class="letter">
    <p class="letter-date">01 January 2050</p>
    <p class="letter-recipient">Company (Pvt) Ltd.<br>PO Box 3355 Mainville St<br>Sample City Country 3355</p>
    <p class="letter-greeting">Dear Daniel Ashworth,</p>
    <div class="letter-body">
      <p>Lorem ipsum dolor sit amet, consectetuer adipiscing elit, sed diam nonummy nibh euismod tincidunt ut laoreet dolore magna aliquam erat volutpat. Ut wisi enim ad minim veniam, quis nostrud exerci tation ullamcorper suscipit lobortis nisl ut aliquip ex ea commodo consequat. Duis dolore te feugait nulla facilisi. Nam liber tempor cum soluta nobis eleifend option congue nihil imperdiet doming id quod mazim placerat facer possim assum. Lorem ipsum dolor sit amet, consectetuer adipiscing elit, sed diam nonummy nibh euismod tincidunt ut laoreet dolore magna aliquam erat volutpat. Ut wisi enim ad minim veniam, quis nostrud exerci tation ullamcorper suscipit lobortis nisl ut aliquip ex ea commodo consequat.</p>
      <p>Consectetuer adipiscing elit, sed diam nonummy nibh euismod tincidunt ut laoreet dolore magna aliquam erat volutpat. Ut wisi enim ad minim veniam, quis nostrud exerci tation ullamcorper suscipit lobortis nisl ut aliquip ex ea commodo consequat. Consectetuer adipiscing elit, sed diam nonummy nibh euismod tincidunt ut laoreet dolore magna aliquam erat volutpat. Ut wisi enim ad minim veniam, quis nostrud exerci tation ullamcorper suscipit lobortis nisl ut aliquip ex ea commodo consequat.</p>
      <p>Consectetuer adipiscing elit, sed diam nonummy nibh euismod tincidunt ut laoreet dolore magna aliquam erat volutpat. Ut wisi enim ad minim veniam, quis nostrud exerci tation ullamcorper suscipit lobortis nisl ut aliquip ex ea commodo consequat. Consectetuer adipiscing elit, sed diam nonummy nibh euismod tincidunt ut laoreet dolore magna aliquam erat volutpat. Ut wisi enim ad minim veniam, quis nostrud exerci tation ullamcorper suscipit lobortis nisl ut aliquip ex ea commodo consequat.</p>
    </div>
    <p class="letter-closing">Sincerely Yours</p>
    <p class="letter-signature">Thomas Reardon</p>
  </article>

  <footer>
    <span class="footer-rule"></span>
    <span class="footer-band"></span>
  </footer>
</main>
</body>
</html>
```